New Business Cards for Tormin Group

We need a new Business Card to compliment our new logo. We are a vibrant design, manufacture and install business providing recreation areas, public parks and Municipal spaces. We want business cards that are classy, modern and clean.

We have recently changed our logo, and are celebrating our 40th anniversary. We want business cards with a new modern design to reflect our status.

Target Market(s)

Customers

Contact Information for Business Card

We need all the details of our 3 offices as per the business card attached. Please disregard the old logo on the business card, the other three files show our new logo.

Requirements
Must have
• All info as per attached business card but with new logo.
Nice to have

```html
<!DOCTYPE html>
<html lang="en">
<head>
<meta charset="utf-8">
<title>Tormin Group – Business Card</title>
<link href="https://fonts.googleapis.com/css2?family=Exo+2:wght@400;500;600&display=swap" rel="stylesheet">
<style>
  :root {
    --backdrop: #d9d9d9;
    --card: #ffffff;
    --brand-red: #e8323c;
    --ink: #3d3d3f;
    --ink-soft: #5a5a5c;
    --band-text: #ffffff;
  }
  * { box-sizing: border-box; margin: 0; padding: 0; }
  html, body {
    width: 1200px; height: 900px; overflow: hidden;
    background: var(--backdrop);
    font-family: "Exo 2", Arial, sans-serif;
  }
  .stage {
    width: 1200px; height: 900px;
    display: flex; align-items: center; justify-content: center;
  }
  .business-card {
    position: relative;
    width: 1000px; height: 572px;
    background: var(--card);
    box-shadow: 0 6px 24px rgba(0,0,0,0.18);
    overflow: hidden;
  }
  .brand {
    position: absolute; top: 50px; right: 58px;
    display: flex; align-items: center; gap: 22px;
  }
  .brand-mark { width: 150px; height: 150px; border-radius: 50%; background: var(--brand-red); }
  .brand-name {
    font-size: 58px; font-weight: 600; color: var(--ink);
    line-height: 0.95; letter-spacing: 1px;
  }
  .person { position: absolute; left: 62px; top: 168px; white-space: nowrap; }
  .person-name {
    font-size: 36px; font-weight: 500; color: var(--brand-red);
    text-transform: uppercase; letter-spacing: 1px; line-height: 1.15;
  }
  .person-title {
    font-size: 19px; color: var(--ink-soft);
    text-transform: uppercase; margin-top: 2px; letter-spacing: 0.5px;
  }
  .person-contact { margin-top: 16px; font-size: 21px; color: var(--ink); line-height: 1.35; }
  .office {
    position: absolute; font-size: 19px; color: var(--ink);
    line-height: 1.32; white-space: nowrap;
  }
  .office-title { font-size: 25px; font-weight: 500; color: var(--brand-red); margin-bottom: 2px; line-height: 1.2; }
  .office--head { left: 62px; top: 350px; }
  .office--dubai { left: 405px; top: 296px; }
  .office--qatar { left: 700px; top: 232px; }
  .web-band {
    position: absolute; left: 0; right: 0; bottom: 0; height: 58px;
    background: var(--brand-red);
    display: flex; align-items: center; justify-content: flex-end;
    padding-right: 40px;
    color: var(--band-text); font-size: 22px; letter-spacing: 0.5px;
  }
</style>
</head>
<body>
<main class="stage">
  <article class="business-card">
    <div class="brand">
      <div class="brand-mark" aria-hidden="true"></div>
      <div class="brand-name">TORMIN<br>GROUP</div>
    </div>

    <section class="person">
      <h1 class="person-name">Rami Halabi</h1>
      <p class="person-title">Managing Partner</p>
      <p class="person-contact">M: +971(0) 50 418 7724<br>rami@tormingroup.com</p>
    </section>

    <section class="office office--head">
      <h2 class="office-title">Head Office</h2>
      <p>P.O. Box 31408 Abu Dhabi, U.A.E.<br>T: +971 (0) 2 5583901<br>F: +971 (0) 2 5583902<br>sales@tormingroup.com</p>
    </section>

    <section class="office office--dubai">
      <h2 class="office-title">Dubai Office</h2>
      <p>P.O. Box 207714 Dubai U.A.E.<br>T: +971 (0) 4 3376210<br>F: +971 (0) 4 3376211<br>sales@tormingroup.com</p>
    </section>

    <section class="office office--qatar">
      <h2 class="office-title">Qatar Office</h2>
      <p>P.O. Box 18833 Doha Qatar<br>T: +974 44715630<br>F: +974 44715631<br>sales@tormingroup.com</p>
    </section>

    <footer class="web-band">www.tormingroup.com</footer>
  </article>
</main>
</body>
</html>
```